American cannabis tech company business card design

Pavrel.com is seeking a modern, professional, and brand-aligned business card that represents our company and its core values: Mission, Story, Values, and Impact. As an innovative cannabis company, we want a business card that is not only visually appealing but also serves as a representation of who we are and what we stand for.

Project Scope: Design a double-sided business card that integrates our brand identity and core values. Incorporate our key brand elements, ensuring a sleek and contemporary aesthetic. Visually reflect our core values (Mission, Story, Values, Impact) in a way that is engaging yet professional.

Target Market(s)

Vendors, third parties,

Contact Information for Business Card

Contact details (name, title, email, phone, website, etc.)

Font styles to use
Other font styles liked:
• Caslon, Centra

Colors

Designer to choose colors to be used in the design.

Requirements
Must have
• Pavrel.com logo and branding A creative yet clean way to integrate our core values (Mission, Story, Values, Impact) Modern typography and a well-structured layout
Nice to have
• forest green, grey, white, black
Should not have
• references to marijuana, leafs, plants, or related product

```html
<!DOCTYPE html>
<html lang="en">
<head>
<meta charset="UTF-8">
<title>Pavrel.com Business Card</title>
<link href="https://fonts.googleapis.com/css2?family=Libre+Caslon+Text:wght@400;700&family=Montserrat:wght@400;500&display=swap" rel="stylesheet">
<style>
  :root {
    --forest: #253f27;
    --forest-deep: #1d3420;
    --forest-bright: #237a38;
    --paper: #ffffff;
    --cream: #f6f3ec;
    --ink: #1c1c1c;
    --stage: #2a2a2a;
  }
  * { margin: 0; padding: 0; box-sizing: border-box; }
  html, body { width: 1200px; height: 900px; overflow: hidden; }
  body {
    background: var(--stage);
    display: flex;
    flex-direction: column;
    align-items: center;
    justify-content: center;
    gap: 40px;
  }
  .card {
    width: 700px;
    height: 400px;
    border-radius: 28px;
    overflow: hidden;
    position: relative;
  }
  .card-front {
    background: linear-gradient(160deg, var(--forest-deep), var(--forest));
    display: flex;
    align-items: center;
    justify-content: center;
  }
  .front-wordmark {
    font-family: "Libre Caslon Text", serif;
    font-weight: 700;
    font-size: 120px;
    letter-spacing: 2px;
    color: var(--forest-bright);
  }
  .card-back {
    background: var(--paper);
    display: flex;
  }
  .back-info {
    flex: 1;
    padding: 52px 0 40px 52px;
    display: flex;
    flex-direction: column;
    justify-content: space-between;
  }
  .holder-name {
    font-family: "Libre Caslon Text", serif;
    font-weight: 700;
    font-size: 26px;
    color: var(--forest);
  }
  .holder-title {
    font-family: "Libre Caslon Text", serif;
    font-weight: 700;
    font-size: 13px;
    color: var(--ink);
    margin-top: 4px;
    margin-left: 16px;
  }
  .contact {
    font-family: "Montserrat", sans-serif;
    font-size: 16px;
    color: var(--ink);
    line-height: 1.3;
  }
  .address { margin-bottom: 18px; }
  .contact-list { list-style: none; }
  .contact-list li {
    display: flex;
    align-items: center;
    gap: 10px;
    margin-top: 6px;
  }
  .contact-icon { width: 14px; height: 14px; fill: var(--forest); flex: none; }
  .brand-band {
    width: 180px;
    background: var(--forest);
    display: flex;
    align-items: center;
    justify-content: center;
  }
  .band-wordmark {
    font-family: "Libre Caslon Text", serif;
    font-weight: 700;
    font-size: 74px;
    color: var(--cream);
    writing-mode: vertical-rl;
    letter-spacing: 2px;
  }
</style>
</head>
<body>
  <section class="card card-front">
    <span class="front-wordmark">PAVREL</span>
  </section>

  <section class="card card-back">
    <div class="back-info">
      <header>
        <h1 class="holder-name">Daniel Hart</h1>
        <p class="holder-title">Owner</p>
      </header>
      <div class="contact">
        <p class="address">418 Linden Row, Suite 12<br>Fairmont, OH 43210</p>
        <ul class="contact-list">
          <li>
            <svg class="contact-icon" viewBox="0 0 24 24"><path d="M6.6 10.8a15 15 0 0 0 6.6 6.6l2.2-2.2a1 1 0 0 1 1-.25 11.4 11.4 0 0 0 3.6.57 1 1 0 0 1 1 1V20a1 1 0 0 1-1 1A17 17 0 0 1 3 4a1 1 0 0 1 1-1h3.5a1 1 0 0 1 1 1c0 1.25.2 2.45.57 3.6a1 1 0 0 1-.25 1z"/></svg>
            555-318-0427
          </li>
          <li>
            <svg class="contact-icon" viewBox="0 0 24 24"><path d="M2 5h20v14H2z M2 5l10 8 10-8" fill="none" stroke="#253f27" stroke-width="2.4"/></svg>
            info@pavrel.com
          </li>
          <li>
            <svg class="contact-icon" viewBox="0 0 24 24"><circle cx="12" cy="12" r="10" fill="none" stroke="#253f27" stroke-width="2.4"/><path d="M2 12h20M12 2c3 3 3 17 0 20M12 2c-3 3-3 17 0 20" fill="none" stroke="#253f27" stroke-width="2"/></svg>
            www.pavrel.com
          </li>
        </ul>
      </div>
    </div>
    <div class="brand-band">
      <span class="band-wordmark">PAVREL</span>
    </div>
  </section>
</body>
</html>
```